Wordpress Powered Website. Outstanding Design Required. Using Morvenic Theme

Designers will not need to create anything other than the home page but there are some design elements on the home page which also need to be factored in: 6 product place holders and 2-3 slides for a slideshow (with images I provide).

Designers will need to familiarise themselves with the Morvenic theme to make sure that their design will work within the theme.

The winning designer will set up all the pages and navigation in place. This includes social media icons, favicon, widgets, etc. In other words, the home page needs to be designed and coded and the other preset theme pages need to be organised in a way that we can start using the website on completion of the job.

Most of the designs I had last time were too colourful. This needs to be subtle not in your face.

Background to the business/website:
Ridgeway Banners is a new Australian venture which will sell large format printed banners and other signage. The market is very competitive so it is important to stand out visually and to have a website which is clean, easy to navigate and easy to order. It will be a combination of online sales and assisted sales but all sales enquiries will come from the website.

As our business is focused on presentation it is vital to have excellent design.
Purchased theme is Morvenic. Only this theme is to be used.

1. A home page using all the preset features of the Morvenic theme - it will just be basically taking my wireframe and inputting it to the live theme.
2. A three slide slideshow, ideally with an edited video. The static image slides can be provided by me during the handover. Placeholder for now.
Similar to this one: http://thecedarhollow.example.au/

Attached is the logo which must be utilised, although it could also sit on a dark background. There is our mascot as well which can be used but does not have to be included.

Target Market(s)

Primarily B2B (business to business)
Main industries will be Construction, Retail, Community, Events & Trade Shows

Industry/Entity Type

Printing

Coding

Coded - Design and coding required

Font styles to use
Sans Serif

Requirements
Must have
• Must have the design files made to web pages within the Wordpress environment.
Nice to have
• Clean design. Stand out from competitors based on design.
Should not have
• Should not look like any competitor

```html
<!DOCTYPE html>
<html lang="en">
<head>
<meta charset="utf-8">
<title>Ridgeway Banners – Home</title>
<link rel="stylesheet" href="https://fonts.googleapis.com/css2?family=Open+Sans:wght@400;600;700&family=Raleway:wght@400;600;800&display=swap">
<style>
:root{
  --red:#e3262c;
  --red-dark:#b81a20;
  --ink:#333333;
  --muted:#8a8a8a;
  --light:#ededed;
  --dark:#2a2a2a;
  --darker:#1c1c1c;
  --footer:#242424;
  --blue:#1f7fd1;
  --green:#4caf3e;
  --orange:#f2921f;
  --white:#ffffff;
}
*{box-sizing:border-box;margin:0;padding:0}
html,body{width:1200px;height:2572px;overflow:hidden}
body{font-family:"Open Sans",Arial,sans-serif;color:var(--ink);background:var(--white);position:relative}
.abs{position:absolute}

/* header */
.site-header{position:absolute;left:0;top:0;width:1200px;height:80px;background:var(--white);border-bottom:1px solid #e4e4e4}
.brand{position:absolute;left:40px;top:22px;display:flex;align-items:center;gap:10px;font-family:"Raleway",sans-serif;font-weight:800;font-size:26px;color:var(--red);letter-spacing:.5px}
.brand-mark{width:22px;height:22px;background:var(--red)}
.contact-bar{position:absolute;right:40px;top:8px;display:flex;gap:26px;font-size:11px;color:var(--muted)}
.contact-bar span{display:flex;align-items:center;gap:6px}
.main-nav{position:absolute;right:40px;top:40px;display:flex;gap:34px;font-size:12px;font-weight:600;color:#555}
.main-nav a{color:inherit;text-decoration:none;padding-bottom:6px}
.main-nav a.active{color:var(--ink);border-bottom:2px solid var(--red)}

/* hero */
.hero{position:absolute;left:0;top:80px;width:1200px;height:480px;background:linear-gradient(180deg,#e93a34 0%,var(--red) 55%,#cf1f26 100%)}
.hero-mascot{position:absolute;left:170px;top:40px;width:240px;height:420px;border-radius:40px;background:radial-gradient(circle at 50% 40%,#a8682f 0%,#7a4520 55%,rgba(122,69,32,0) 75%)}
.hero-kicker{position:absolute;left:560px;top:40px;width:520px;text-align:center;font-family:"Raleway",sans-serif;font-size:32px;color:var(--white)}
.hero-ribbon{position:absolute;left:530px;top:92px;width:560px;height:62px;background:var(--white);display:flex;align-items:center;justify-content:center;font-family:"Raleway",sans-serif;font-weight:800;font-size:34px;letter-spacing:2px;color:var(--red)}
.hero-list{position:absolute;left:580px;top:180px;list-style:none;color:var(--white);font-size:17px;line-height:32px}
.hero-list li{display:flex;align-items:center;gap:12px}
.hero-list li::before{content:"";width:9px;height:9px;border-radius:50%;background:var(--white)}
.hero-list b{color:#ffe14a;font-weight:700}
.slide-arrow{position:absolute;top:215px;width:32px;height:44px;background:rgba(255,255,255,.55);display:flex;align-items:center;justify-content:center}
.slide-arrow.prev{left:0}
.slide-arrow.next{right:0}

/* services */
.services{position:absolute;left:0;top:560px;width:1200px;height:440px;background:var(--white)}
.services-ghost{position:absolute;left:0;top:22px;width:1200px;text-align:center;font-family:"Raleway",sans-serif;font-size:120px;font-weight:400;color:#f1f1f1;letter-spacing:6px;line-height:1}
.section-title{position:absolute;left:0;width:1200px;text-align:center;font-family:"Raleway",sans-serif;font-size:26px;color:var(--ink);letter-spacing:1px}
.section-title::after{content:"";display:block;width:50px;height:2px;background:var(--red);margin:10px auto 0}
.service{position:absolute;top:130px;width:230px;height:250px;text-align:center;padding-top:18px}
.service.featured{border:1px solid #d8d8d8;box-shadow:0 2px 6px rgba(0,0,0,.06)}
.service-icon{width:110px;height:110px;border-radius:50%;margin:0 auto;display:flex;align-items:center;justify-content:center;border:5px solid}
.service-icon .dot{width:70px;height:70px;border-radius:50%;display:flex;align-items:center;justify-content:center}
.service h3{margin-top:24px;font-size:15px;font-weight:700;color:var(--ink)}
.service p{margin:8px 14px 0;font-size:11px;line-height:16px;color:var(--muted)}

/* guarantees */
.guarantees{position:absolute;left:0;top:1010px;width:1200px;height:540px;background:linear-gradient(180deg,#303030 0%,#262626 60%,#202020 100%)}
.tabs{position:absolute;left:0;top:0;width:1200px;height:64px;border-bottom:1px solid #444}
.tab{position:absolute;top:22px;font-size:14px;font-weight:600;color:#cfcfcf;letter-spacing:1px}
.tab.current{top:0;height:64px;width:190px;background:var(--red);color:var(--white);display:flex;align-items:center;justify-content:center}
.perk{position:absolute;width:470px;display:flex;gap:22px}
.perk-icon{flex:0 0 70px;height:70px;border-radius:50%;background:var(--white);display:flex;align-items:center;justify-content:center}
.perk h4{font-size:20px;font-weight:700;color:var(--white);margin-bottom:10px}
.perk p{font-size:12px;line-height:19px;color:#a9a9a9}
.rainbow{position:absolute;left:0;top:1550px;width:1200px;height:8px;background:linear-gradient(90deg,#e3262c 0 16%,#f2921f 16% 32%,#f6d22a 32% 48%,#4caf3e 48% 64%,#1f7fd1 64% 80%,#8a3fbf 80% 100%)}

/* custom printing */
.printing{position:absolute;left:0;top:1558px;width:1200px;height:722px;background:var(--light)}
.printing h2{position:absolute;left:0;top:80px;width:1200px;text-align:center;font-family:"Raleway",sans-serif;font-weight:400;font-size:30px;color:#555;letter-spacing:1px}
.printing .accent{position:absolute;left:0;top:130px;width:1200px;display:flex;justify-content:center;align-items:center;gap:20px;font-family:"Raleway",sans-serif;font-weight:800;font-size:32px;color:var(--red);letter-spacing:1px}
.printing .accent::before,.printing .accent::after{content:"";width:70px;height:2px;background:var(--red)}
.printing p{position:absolute;left:200px;top:196px;width:800px;text-align:center;font-size:15px;line-height:24px;color:#666}
.showcase{position:absolute;left:230px;top:290px;width:740px;height:400px;background:radial-gradient(ellipse at 50% 45%,#4a6fa0 0%,#1e2c44 45%,rgba(237,237,237,0) 72%)}

/* footer */
.site-footer{position:absolute;left:0;top:2280px;width:1200px;height:292px;background:var(--footer);color:#bdbdbd}
.foot-col{position:absolute;top:36px}
.foot-col h5{font-size:13px;font-weight:700;color:var(--white);letter-spacing:1px;margin-bottom:14px}
.foot-col ul{list-style:none;font-size:11px;line-height:20px}
.foot-col li::before{content:"› ";color:var(--red)}
.social{display:flex;gap:10px}
.social span{width:30px;height:30px;background:#4a4a4a;display:block}
.foot-bottom{position:absolute;left:0;bottom:0;width:1200px;height:80px;background:var(--darker);border-top:1px solid #333}
.badge{position:absolute;top:22px;display:flex;align-items:center;gap:10px;font-size:10px;line-height:14px;font-weight:700;color:#d0d0d0}
.badge i{width:34px;height:34px;border-radius:50%;border:2px solid #777;display:block}
.copyright{position:absolute;right:40px;top:32px;font-size:11px;color:#8a8a8a}
</style>
</head>
<body>

<header class="site-header">
  <div class="brand"><span class="brand-mark"></span>Ridgeway Banners</div>
  <div class="contact-bar">
    <span><svg width="10" height="13" viewBox="0 0 10 13"><path d="M5 0a5 5 0 0 0-5 5c0 3.5 5 8 5 8s5-4.5 5-8a5 5 0 0 0-5-5zm0 7a2 2 0 1 1 0-4 2 2 0 0 1 0 4z" fill="#e3262c"/></svg>Melbourne Victoria</span>
    <span><svg width="13" height="10" viewBox="0 0 13 10"><rect x=".5" y=".5" width="12" height="9" fill="none" stroke="#e3262c"/><path d="M.5 .5l6 5 6-5" fill="none" stroke="#e3262c"/></svg>info@ridgewaybanners.example.au</span>
    <span><svg width="11" height="11" viewBox="0 0 11 11"><path d="M2 0l2 2.5-1.2 1.4a7 7 0 0 0 4.3 4.3L8.5 7 11 9l-1.5 2C4.5 11 0 6.5 0 1.5z" fill="#e3262c"/></svg>Phone: 1300 555 014</span>
  </div>
  <nav class="main-nav">
    <a class="active" href="#">HOME</a><a href="#">BANNERS</a><a href="#">FLAGS</a><a href="#">BANNERS STANDS</a><a href="#">ABOUT US</a><a href="#">FAQS</a>
  </nav>
</header>

<section class="hero">
  <div class="hero-mascot" role="img" aria-label="Company mascot giving a thumbs up"></div>
  <div class="hero-kicker">Over 95%</div>
  <div class="hero-ribbon">CUSTOMERS RECOMMEND</div>
  <ul class="hero-list">
    <li>Free Hem and Eyelets</li>
    <li>No Set-up Fee</li>
    <li>Same Day Shipping on most orders</li>
    <li>Pay after proof</li>
    <li>Custom Vinyl Banners Starting Price&nbsp;<b>START ORDER</b></li>
  </ul>
  <div class="slide-arrow prev"><svg width="12" height="18" viewBox="0 0 12 18"><path d="M10 1L2 9l8 8" fill="none" stroke="#555" stroke-width="3"/></svg></div>
  <div class="slide-arrow next"><svg width="12" height="18" viewBox="0 0 12 18"><path d="M2 1l8 8-8 8" fill="none" stroke="#555" stroke-width="3"/></svg></div>
</section>

<section class="services">
  <div class="services-ghost">OUR SERVICES</div>
  <h2 class="section-title" style="top:48px">OUR SERVICES</h2>

  <div class="service" style="left:65px">
    <div class="service-icon" style="border-color:var(--blue)"><div class="dot" style="background:var(--blue)"><svg width="34" height="34" viewBox="0 0 34 34"><path d="M6 28l4-10L24 4l6 6-14 14z" fill="#fff"/></svg></div></div>
    <h3>Free Design Service</h3>
    <p>Every vinyl banner order includes a free basic layout. Our skilled graphic designers turn your ideas into print.</p>
  </div>
  <div class="service featured" style="left:355px">
    <div class="service-icon" style="border-color:var(--green)"><div class="dot" style="background:var(--green)"><svg width="34" height="34" viewBox="0 0 34 34"><path d="M6 18l7 7L28 9" fill="none" stroke="#fff" stroke-width="5"/></svg></div></div>
    <h3>Ensure Quality</h3>
    <p>Every banner is checked by hand before dispatch. Our trained print team make sure colours match your proof.</p>
  </div>
  <div class="service" style="left:630px">
    <div class="service-icon" style="border-color:var(--orange)"><div class="dot" style="background:var(--orange)"><svg width="36" height="26" viewBox="0 0 36 26"><path d="M0 2h22v16H0zM22 8h8l6 6v4H22z" fill="#fff"/><circle cx="8" cy="21" r="4" fill="#fff"/><circle cx="28" cy="21" r="4" fill="#fff"/></svg></div></div>
    <h3>Fast Delivery</h3>
    <p>Most orders are printed and shipped the same day. Our local couriers bring your signs to site on time.</p>
  </div>
  <div class="service" style="left:905px">
    <div class="service-icon" style="border-color:var(--red)"><div class="dot" style="background:var(--red)"><svg width="30" height="30" viewBox="0 0 30 30"><path d="M2 2h12l14 14-12 12L2 14z" fill="#fff"/><circle cx="9" cy="9" r="3" fill="#e3262c"/></svg></div></div>
    <h3>Price Guarantee</h3>
    <p>Find a lower quote for the same banner and we will match it. Our fair pricing keeps your budget on track.</p>
  </div>
</section>

<section class="guarantees">
  <div class="tabs">
    <span class="tab" style="left:300px">POPULAR</span>
    <span class="tab current" style="left:470px">NEW ARRIVALS</span>
    <span class="tab" style="left:850px">BEST SELLERS</span>
  </div>

  <div class="perk" style="left:110px;top:120px">
    <div class="perk-icon"><svg width="30" height="30" viewBox="0 0 30 30"><path d="M4 16l7 7L26 7" fill="none" stroke="#e3262c" stroke-width="4"/></svg></div>
    <div><h4>100% Quality Guarantee</h4><p>We stand behind every banner we print and offer reprints or refunds on faulty work. If a mistake is ours, we will quickly send you a fresh print.</p></div>
  </div>
  <div class="perk" style="left:650px;top:120px">
    <div class="perk-icon"><svg width="30" height="30" viewBox="0 0 30 30"><path d="M2 2h12l14 14-12 12L2 14z" fill="#e3262c"/><circle cx="9" cy="9" r="3" fill="#fff"/></svg></div>
    <div><h4>Best Price Guarantee</h4><p>We stand behind every banner we print and offer reprints or refunds on faulty work. If a mistake is ours, we will quickly send you a fresh print.</p></div>
  </div>
  <div class="perk" style="left:110px;top:320px">
    <div class="perk-icon"><svg width="34" height="24" viewBox="0 0 36 26"><path d="M0 2h22v16H0zM22 8h8l6 6v4H22z" fill="#e3262c"/><circle cx="8" cy="21" r="4" fill="#e3262c"/><circle cx="28" cy="21" r="4" fill="#e3262c"/></svg></div>
    <div><h4>Free Shipping</h4><p>We stand behind every banner we print and offer reprints or refunds on faulty work. If a mistake is ours, we will quickly send you a fresh print.</p></div>
  </div>
  <div class="perk" style="left:650px;top:320px">
    <div class="perk-icon"><svg width="28" height="30" viewBox="0 0 28 30"><rect x="2" y="2" width="24" height="26" fill="none" stroke="#e3262c" stroke-width="3"/><path d="M7 10h14M7 15h14M7 20h9" stroke="#e3262c" stroke-width="2"/></svg></div>
    <div><h4>Free Design Proofs</h4><p>We stand behind every banner we print and offer reprints or refunds on faulty work. If a mistake is ours, we will quickly send you a fresh print.</p></div>
  </div>
</section>
<div class="rainbow"></div>

<section class="printing">
  <h2>CUSTOM BANNER PRINTING, DISPLAYS</h2>
  <div class="accent">SIGNS &amp; GRAPHICS</div>
  <p>Our Banners are constructed of durable vinyl and printed with the latest technology in commercial printers. We provide a wide range of banner sizes – up to 100 feet long.</p>
  <div class="showcase" role="img" aria-label="Monitor showing banner samples with film strips of printed work"></div>
</section>

<footer class="site-footer">
  <div class="foot-col" style="left:60px"><h5>MAIN MENU</h5><ul><li>Home</li><li>What's New?</li><li>Featured</li><li>Top sellers</li></ul></div>
  <div class="foot-col" style="left:280px"><h5>EXTRAS</h5><ul><li>Specials</li><li>Brands</li><li>Reviews</li></ul></div>
  <div class="foot-col" style="left:490px"><h5>INFORMATION</h5><ul><li>Privacy Policy</li><li>Conditions</li><li>Terms &amp; Conditions</li><li>Contact Us</li></ul></div>
  <div class="foot-col" style="left:710px"><h5>YOUR ACCOUNT</h5><ul><li>Shipping &amp; Returns</li><li>Advanced Search</li><li>Create an Account</li><li>Log In</li></ul></div>
  <div class="foot-col" style="left:960px"><h5>FOLLOW US ON</h5><div class="social"><span></span><span></span><span></span></div></div>

  <div class="foot-bottom">
    <div class="badge" style="left:60px"><i></i><span>SATISFACTION<br>100% GUARANTEED</span></div>
    <div class="badge" style="left:260px"><i></i><span>FREE SHIPPING<br>ON ORDERS OVER $99</span></div>
    <div class="badge" style="left:470px"><i></i><span>7 DAY<br>EASY RETURN</span></div>
    <div class="copyright">Copyright © 2016 Ridgeway Banners. All Rights Reserved</div>
  </div>
</footer>

</body>
</html>
```